Teach English in China Website Redesign Needed

We recruit native English speakers from the US, UK, etc. who want to teach English as a foreign language in schools in China. Our target customer is college educated, age 22-28 and they love to travel. We prefer designs with bright colors and lots of photos. We want to keep all the text on our current homepage, BrightLanternPost.com. We are open to changing our logo. A competitor's page that we like is pinemeadowtutors.com because of their bright colors, photos and use of white space. We are happy to give you a dofollow link and design credit on our homepage. The use of included photos is optional. We need at least a home page design and a standard blog post design.
Target Market(s)
Our target customer is college educated, age 22-28 and they love to travel. Half of our customers are kindergarten teachers. Half of our customers are male.
Logo Text
Bright Lantern Post
Requirements
Must have
- Bright colors
Should not have
- Our homepage must not look crowded. Use white space effectively.

```html
<!DOCTYPE html>
<html lang="en">
<head>
<meta charset="utf-8">
<title>Bright Lantern Post — Teach English in China</title>
<link href="https://fonts.googleapis.com/css2?family=Rajdhani:wght@400;500;600;700&family=Didact+Gothic&display=swap" rel="stylesheet">
<style>
  :root {
    --orange: #ff5a00;
    --lime: #c6ff6a;
    --yellow: #fff86a;
    --green: #4f8a10;
    --ink: #222;
    --body: #444;
    --hero-top: #6a4d7a;
    --hero-mid: #7c2f9a;
    --hero-low: #3b2a40;
    --dot: #c8c24a;
  }
  * { margin: 0; padding: 0; box-sizing: border-box; }
  html, body { width: 1179px; height: 1200px; overflow: hidden; background: #fff; }
  body { font-family: "Rajdhani", sans-serif; color: var(--body); position: relative; }

  .topbar { position: absolute; left: 0; top: 0; width: 1179px; height: 34px; background: var(--orange); }
  .follow { position: absolute; right: 86px; top: 10px; color: #fff; font-size: 13px; font-weight: 500; display: flex; align-items: center; gap: 9px; }
  .follow .social { width: 10px; height: 10px; border-radius: 50%; background: #fff; opacity: .9; }

  .contact { position: absolute; right: 86px; top: 52px; display: flex; align-items: center; gap: 14px; font-size: 20px; font-weight: 500; color: #333; }
  .contact .sep { margin: 0 4px; }
  .contact svg { vertical-align: -3px; margin-right: 4px; }

  .navbar { position: absolute; left: 0; top: 95px; width: 1179px; height: 44px; background: var(--yellow); }
  .nav { position: absolute; right: 86px; top: 0; display: flex; gap: 0; list-style: none; }
  .nav li { font-size: 13px; font-weight: 600; color: #222; height: 44px; line-height: 44px; margin-left: 67px; position: relative; }
  .nav li.active { color: var(--orange); }
  .nav li.active::after { content: ""; position: absolute; left: 0; right: 0; bottom: 0; height: 3px; background: var(--orange); }

  .brand { position: absolute; left: 86px; top: 0; width: 254px; height: 138px; background: var(--lime); box-shadow: 0 0 4px rgba(0,0,0,.25); display: flex; align-items: center; justify-content: center; gap: 10px; z-index: 2; }
  .brand .mark { width: 16px; height: 16px; border-radius: 50%; background: var(--orange); flex: none; }
  .brand .name { font-size: 30px; font-weight: 700; line-height: 1; color: var(--ink); width: 150px; }

  .hero { position: absolute; left: 0; top: 139px; width: 1179px; height: 540px; background: linear-gradient(180deg, var(--hero-top) 0%, var(--hero-mid) 45%, var(--hero-low) 100%); }
  .hero-text { position: absolute; left: 87px; top: 276px; font-family: "Didact Gothic", sans-serif; font-size: 25px; line-height: 35px; color: #fff; text-shadow: 0 1px 3px rgba(0,0,0,.5); }
  .hero-text strong { color: #ffef3a; font-weight: 700; font-family: "Rajdhani", sans-serif; font-size: 28px; letter-spacing: .3px; }
  .dots { position: absolute; left: 552px; top: 484px; display: flex; gap: 9px; }
  .dots span { width: 11px; height: 11px; border-radius: 50%; background: var(--dot); }
  .dots span.on { background: var(--orange); box-shadow: 0 0 0 2px #ffe24a; }

  .intro { position: absolute; left: 88px; top: 736px; width: 1004px; text-align: center; }
  .intro h1 { font-size: 38px; font-weight: 700; color: var(--green); letter-spacing: .5px; margin-bottom: 30px; }
  .intro h1 span { color: var(--orange); }
  .intro p { font-size: 14px; line-height: 22.7px; margin-bottom: 22px; color: #4a4a4a; }
</style>
</head>
<body>
  <header>
    <div class="topbar">
      <div class="follow">Follow us on :
        <span class="social"></span><span class="social"></span><span class="social"></span><span class="social"></span>
      </div>
    </div>
    <div class="brand">
      <span class="mark"></span>
      <span class="name">Bright Lantern Post</span>
    </div>
    <div class="contact">
      <span>
        <svg width="11" height="18" viewBox="0 0 11 18"><rect x="1" y="1" width="9" height="16" rx="1.5" fill="none" stroke="#222" stroke-width="2"/><rect x="2" y="3" width="7" height="10" fill="#222"/></svg>555-013-4872
      </span>
      <span class="sep">|</span>
      <span>
        <svg width="22" height="20" viewBox="0 0 22 20"><path d="M1 9 L21 1 L14 19 L10 12 Z M10 12 L21 1" fill="none" stroke="#222" stroke-width="2" stroke-linejoin="round"/></svg>Mara@LanternPostJobs.com
      </span>
    </div>
    <nav class="navbar">
      <ul class="nav">
        <li class="active">HOME</li>
        <li>AVAILABLE JOBS</li>
        <li>APPLY ONLINE</li>
        <li>BLOG</li>
        <li>FAQ</li>
        <li>CONTACT</li>
      </ul>
    </nav>
  </header>

  <section class="hero" role="img" aria-label="Photo of students in purple shirts stretching in a gym">
    <div class="hero-text">
      WE ARE SEEKING ENGLISH SPEAKERS FROM THE<br>
      <strong>US, UK, CANADA, IRELAND, AUSTRALIA, NEW ZEALAND AND SOUTH AFRICA</strong><br>
      TO TEACH ENGLISH IN CHINA
    </div>
    <div class="dots"><span class="on"></span><span></span><span></span><span></span></div>
  </section>

  <main class="intro">
    <h1>TEACH ENGLISH IN <span>CHINA</span></h1>
    <p>Want to teach English in China? Do you enjoy teaching children or adults? Would you like the adventure of teaching in China for a year? Then we have the perfect job for you! We are seeking English speakers from the US, UK, Canada, Ireland, Australia, New Zealand and South Africa to teach English in China for a year (or longer if you wish). We recruit for hundreds of schools all over China such as Harbor English, Maple Lane English, Corwin English, Bellfield English, Sunbeam Corner, Kitebright Kids, Silver Pear, public schools, international schools, universities, and more.</p>
    <p>Don’t want to fly to China alone? No problem, fly over with other new teachers and our American Director, Mara Ellison. She’ll help you get settled and adjusted to Chinese culture. We take EXCELLENT care of our teachers with ongoing American and local support for your entire year in China.</p>
    <p>A Bachelor’s degree and experience is recommended, but a degree is not required to teach kindergarten. If you have a Bachelor’s degree, you also have the option to teach older children and adults. Also, more good news is that you do NOT need to know how to speak Chinese. Also, we provide FREE TEFL / TESOL 120-hour online certification to all the teachers we place.</p>
    <p>Many people who choose to teach English in China, do so because of it’s so beautiful, fascinating and exotic. China is in an enormous country with a diverse geography, climate, and people groups. Teaching English in China gives you the opportunity to explore China and other Asian countries on your days off and take holidays like you never could before.</p>
  </main>
</body>
</html>
```